Communication and Marketing agency needs a new presentation card

We are a group of communication and marketing agencies specialized in companies that are in the logistics and industrial sector. The head agency is TELVANO Grupo and the group consists of 4 agencies: TELVANO Media, TELVANO Digital, TELVANO Research and DifundeEnPantalla. We hace 4 offices in Spain (Madrid, Barcelona, Valencia and Murcia). We are looking for a clean and attractive design that transmits our experience, brand presence in the market and knowledge to those who receive the card.It has to maintain the colors of the logo that is attached.
Target Market(s)
logistics and industrial sector
Marketing department
Contact Information for Business Card
Clean and attractive design

```html
<!DOCTYPE html>
<html lang="es">
<head>
<meta charset="utf-8">
<title>DifundeEnPantalla — TELVANO Grupo</title>
<link href="https://fonts.googleapis.com/css2?family=Josefin+Sans:wght@600&display=swap" rel="stylesheet">
<style>
  :root {
    --brand-red: #be202e;
    --map-tint: #c6413f;
    --charcoal: #3a3a3c;
    --white: #ffffff;
  }
  html, body {
    margin: 0;
    padding: 0;
    overflow: hidden;
    background: var(--brand-red);
  }
  .card {
    position: relative;
    width: 1200px;
    height: 686px;
    background: var(--brand-red);
    overflow: hidden;
    font-family: "Josefin Sans", sans-serif;
    font-weight: 600;
    color: var(--white);
  }
  .world-map {
    position: absolute;
    left: 137px;
    top: 103px;
    width: 970px;
    height: 403px;
    background: var(--map-tint);
    border-radius: 120px 160px 140px 100px;
    opacity: 0.75;
  }
  .corner-stripes {
    position: absolute;
    inset: 0;
    width: 1200px;
    height: 686px;
  }
  .headline {
    position: absolute;
    left: 0;
    right: 0;
    top: 255px;
    text-align: center;
    text-transform: uppercase;
    line-height: 1;
  }
  .headline span {
    display: block;
  }
  .headline .line-one {
    font-size: 84px;
    letter-spacing: 6px;
  }
  .headline .line-two {
    font-size: 62px;
    letter-spacing: 3px;
    margin-top: 14px;
  }
  .agencies {
    position: absolute;
    left: 0;
    top: 530px;
    width: 1200px;
    height: 70px;
  }
  .agency {
    position: absolute;
    top: 4px;
    width: 190px;
    margin-left: -95px;
    text-align: right;
    text-transform: uppercase;
    line-height: 1;
  }
  .agency-name {
    display: block;
    font-size: 32px;
    letter-spacing: 1px;
    text-align: center;
  }
  .agency-unit {
    display: block;
    font-size: 17px;
    text-transform: none;
    margin-top: 4px;
    padding-right: 6px;
  }
  .divider {
    position: absolute;
    top: 0;
    width: 1.5px;
    height: 80px;
    background: var(--white);
  }
</style>
</head>
<body>
  <div class="card">
    <div class="world-map" role="img" aria-label="Mapa del mundo en rojo tenue"></div>

    <svg class="corner-stripes" viewBox="0 0 1400 800" preserveAspectRatio="none" aria-hidden="true">
      <polygon points="1020,0 1400,0 1400,380" fill="var(--charcoal)"/>
      <polygon points="985,0 1018,0 1225,207 1225,248" fill="var(--white)"/>
      <polygon points="1058,0 1092,0 1365,273 1365,305" fill="var(--white)"/>
      <polygon points="0,612 0,800 190,800" fill="var(--charcoal)"/>
      <polygon points="45,637 76,637 240,800 205,800" fill="var(--white)"/>
      <polygon points="0,690 0,725 75,800 110,800" fill="var(--white)"/>
    </svg>

    <h1 class="headline">
      <span class="line-one">Difunde</span>
      <span class="line-two">EnPantalla</span>
    </h1>

    <div class="agencies">
      <div class="agency" style="left:223px">
        <span class="agency-name">Telvano</span>
        <span class="agency-unit">Digital</span>
      </div>
      <div class="divider" style="left:340px"></div>
      <div class="agency" style="left:471px">
        <span class="agency-name">Telvano</span>
        <span class="agency-unit">Media</span>
      </div>
      <div class="divider" style="left:605px"></div>
      <div class="agency" style="left:720px">
        <span class="agency-name">Telvano</span>
        <span class="agency-unit">Grupo</span>
      </div>
      <div class="divider" style="left:837px"></div>
      <div class="agency" style="left:969px">
        <span class="agency-name">Telvano</span>
        <span class="agency-unit">Research</span>
      </div>
    </div>
  </div>
</body>
</html>
```